Medical VIP club - small design

Please read the specs in a design brief attached. Also we don't have logo in a Vector format and attaching the only version we have.

Club

```html
<!DOCTYPE html>
<html lang="en">
<head>
<meta charset="utf-8">
<title>Vitaleon – VIP Club</title>
<link href="https://fonts.googleapis.com/css2?family=Arimo:wght@400;700&display=swap" rel="stylesheet">
<style>
:root{
  --page-deep:#1b3a86;
  --page-edge:#2c58b4;
  --brand-blue:#1f78d8;
  --brand-navy:#1a3a8c;
  --tab-top:#4aa2ff;
  --tab-bottom:#0a5bdc;
  --tab-light-top:#5cc4ff;
  --tab-light-bottom:#1f8de8;
  --tab-dark-top:#2a4fe8;
  --tab-dark-bottom:#0a1ec0;
  --panel:#ffffff;
  --panel-line:#e3e6ee;
  --body-text:#4a4a4a;
  --white:#ffffff;
}
*{box-sizing:border-box;margin:0;padding:0}
html,body{width:1200px;height:876px;overflow:hidden}
body{
  position:relative;
  font-family:"Arimo",Arial,sans-serif;
  background:
    linear-gradient(90deg,var(--page-edge) 0,var(--page-deep) 6%,var(--page-deep) 94%,var(--page-edge) 100%);
}
.nav-band{
  position:absolute;left:0;top:241px;width:1200px;height:37px;
  background:linear-gradient(#d4e4ff,#a9c6f6);
}
.header{
  position:absolute;left:24px;top:10px;width:1158px;height:186px;
  border-radius:14px;overflow:hidden;
  background:linear-gradient(90deg,#ffffff 0,#ffffff 28%,#c5d5f2 50%,#7f9fda 56%);
  box-shadow:0 0 0 2px #2a4a9a;
}
.header-photo{
  position:absolute;left:619px;top:0;width:539px;height:186px;
  background:linear-gradient(90deg,rgba(200,215,240,0) 0,#c9d7ea 12%,#9fb8d8 40%,#d8d2c4 70%,#b9a88e 100%);
}
.brand{
  position:absolute;left:22px;top:72px;display:flex;align-items:center;gap:12px;
}
.brand-dot{width:40px;height:40px;border-radius:50%;background:var(--brand-blue)}
.brand-name{font-size:58px;font-weight:700;color:var(--brand-blue);line-height:1}
.phone-icon{position:absolute;left:766px;top:52px}
.phone-number{
  position:absolute;left:892px;top:78px;font-size:41px;font-weight:700;color:var(--brand-navy);
  text-shadow:-2px -2px 0 #fff,2px -2px 0 #fff,-2px 2px 0 #fff,2px 2px 0 #fff;
}
.nav{position:absolute;left:24px;top:208px;display:flex;gap:3px}
.nav-tab{
  width:191px;height:70px;border-radius:12px 12px 0 0;
  display:flex;align-items:center;justify-content:center;
  color:var(--white);font-size:19.5px;
  background:linear-gradient(var(--tab-top) 0,#2b7cf2 48%,var(--tab-bottom) 52%,#1e6ee8 100%);
  box-shadow:inset 0 1px 0 rgba(255,255,255,.5);
  padding-top:6px;
}
.nav-tab.is-current{background:linear-gradient(var(--tab-light-top) 0,#3aa8f4 48%,var(--tab-light-bottom) 52%,#36a0ea 100%)}
.nav-tab.is-highlight{background:linear-gradient(var(--tab-dark-top) 0,#1b3fe0 48%,var(--tab-dark-bottom) 52%,#1c2fd0 100%)}
.panel{
  position:absolute;left:18px;top:288px;width:1170px;height:486px;
  background:var(--panel);border-radius:12px;overflow:hidden;
  box-shadow:0 0 0 2px #3a64bf;
}
.panel-title{
  height:53px;padding-left:27px;display:flex;align-items:center;
  font-size:24px;color:var(--white);
  background:linear-gradient(#5aa2f8 0,#2a7ae8 45%,#0a5ad8 55%,#0b57d0 100%);
}
.entry{display:flex;gap:24px;padding:32px 30px 0 24px}
.entry + .entry{padding-top:27px}
.entry-photo{
  flex:none;width:154px;height:141px;
  background:linear-gradient(160deg,#dfe8f2 0,#8ec0e8 35%,#cfd7c8 65%,#7a6a56 100%);
  box-shadow:2px 3px 5px rgba(0,0,0,.35);border:2px solid #fff;
}
.entry-text{font-size:13.6px;line-height:22px;color:var(--body-text);margin-top:-3px}
.divider{height:1px;background:var(--panel-line);margin:27px 18px 0 26px}
.footer{
  position:absolute;left:18px;top:784px;width:1170px;height:83px;border-radius:12px;
  background:linear-gradient(#6aaaf8 0,#2f7eec 45%,#0a5ad8 55%,#1566e0 100%);
  box-shadow:0 0 0 2px #3a64bf;
}
.social{position:absolute;left:28px;top:24px;display:flex;gap:4px}
.social-square{width:38px;height:38px;border-radius:4px;box-shadow:1px 2px 3px rgba(0,0,0,.35)}
.social-square.one{background:#3b5a9a}
.social-square.two{background:#3fb6e8}
.social-square.three{background:#f0792a}
.copyright{position:absolute;left:0;width:100%;top:38px;text-align:center;font-size:13px;color:var(--white)}
.footer-brand{
  position:absolute;right:34px;top:24px;display:flex;align-items:center;gap:8px;
}
.footer-brand .brand-dot{width:24px;height:24px;background:#cfe2ff}
.footer-brand .brand-name{font-size:36px;color:#cfe2ff}
</style>
</head>
<body>
<div class="nav-band"></div>

<header class="header">
  <div class="header-photo" role="img" aria-label="Bright modern lounge with tall windows overlooking city towers"></div>
  <div class="brand">
    <span class="brand-dot"></span>
    <span class="brand-name">Vitaleon</span>
  </div>
  <svg class="phone-icon" width="88" height="88" viewBox="0 0 88 88" aria-hidden="true">
    <defs>
      <radialGradient id="orb" cx="40%" cy="30%" r="70%">
        <stop offset="0" stop-color="#5e8ef0"/>
        <stop offset="1" stop-color="#0b2a8a"/>
      </radialGradient>
    </defs>
    <circle cx="44" cy="44" r="42" fill="url(#orb)" stroke="#fff" stroke-width="2"/>
    <path d="M20 38c0-8 48-8 48 0v5h-12v-5c-6-2-18-2-24 0v5H20z" fill="#fff"/>
    <path d="M30 44h28l6 20H24z" fill="#fff"/>
    <circle cx="44" cy="55" r="5" fill="#1a3a8c"/>
  </svg>
  <div class="phone-number">555-010-200</div>
</header>

<nav class="nav">
  <div class="nav-tab">About Us</div>
  <div class="nav-tab">VIP Club</div>
  <div class="nav-tab is-current">Services</div>
  <div class="nav-tab">Packages &amp; Prices</div>
  <div class="nav-tab is-highlight">Registration</div>
  <div class="nav-tab">Contacts</div>
</nav>

<main class="panel">
  <h1 class="panel-title" style="font-weight:400">VIP Club</h1>
  <article class="entry">
    <div class="entry-photo" role="img" aria-label="Couple in white robes on a sunny seaside terrace"></div>
    <p class="entry-text">Lorem ipsum dolor sit amet consecutor. Lorem ipsum dolor sit amet consecutor. Lorem ipsum dolor sit amet consecutor. Lorem ipsum dolor sit amet consecutor. Lorem ipsum dolor sit amet consecutor. Lorem ipsum dolor sit amet consecutor. Lorem ipsum dolor sit amet consecutor. Lorem ipsum dolor sit amet consecutor. Lorem ipsum dolor sit amet consecutor. Lorem ipsum dolor sit amet consecutor. Lorem ipsum dolor sit amet consecutor. Lorem ipsum dolor sit amet consecutor. Lorem ipsum dolor sit amet consecutor. Lorem ipsum dolor sit amet consecutor. Lorem ipsum dolor sit amet consecutor. Lorem ipsum dolor sit amet consecutor. Lorem ipsum dolor sit amet consecutor. Lorem ipsum dolor sit amet consecutor. Lorem ipsum dolor sit amet consecutor. Lorem ipsum dolor sit amet consecutor. Lorem ipsum dolor sit amet consecutor. Lorem ipsum dolor sit amet consecutor. Lorem ipsum dolor sit amet consecutor. Lorem ipsum dolor sit amet consecutor. Lorem ipsum dolor sit amet consecutor. Lorem ipsum dolor sit amet consecutor.</p>
  </article>
  <div class="divider"></div>
  <article class="entry">
    <div class="entry-photo" role="img" aria-label="Couple in white robes on a sunny seaside terrace"></div>
    <p class="entry-text">Lorem ipsum dolor sit amet consecutor. Lorem ipsum dolor sit amet consecutor. Lorem ipsum dolor sit amet consecutor. Lorem ipsum dolor sit amet consecutor. Lorem ipsum dolor sit amet consecutor. Lorem ipsum dolor sit amet consecutor. Lorem ipsum dolor sit amet consecutor. Lorem ipsum dolor sit amet consecutor. Lorem ipsum dolor sit amet consecutor. Lorem ipsum dolor sit amet consecutor. Lorem ipsum dolor sit amet consecutor. Lorem ipsum dolor sit amet consecutor. Lorem ipsum dolor sit amet consecutor. Lorem ipsum dolor sit amet consecutor. Lorem ipsum dolor sit amet consecutor. Lorem ipsum dolor sit amet consecutor. Lorem ipsum dolor sit amet consecutor. Lorem ipsum dolor sit amet consecutor. Lorem ipsum dolor sit amet consecutor. Lorem ipsum dolor sit amet consecutor. Lorem ipsum dolor sit amet consecutor. Lorem ipsum dolor sit amet consecutor. Lorem ipsum dolor sit amet consecutor. Lorem ipsum dolor sit amet consecutor. Lorem ipsum dolor sit amet consecutor. Lorem ipsum dolor sit amet consecutor.</p>
  </article>
</main>

<footer class="footer">
  <div class="social">
    <span class="social-square one"></span>
    <span class="social-square two"></span>
    <span class="social-square three"></span>
  </div>
  <p class="copyright">Copyright ©2010 Vitaleon. All Rights Reserved</p>
  <div class="footer-brand">
    <span class="brand-dot"></span>
    <span class="brand-name">Vitaleon</span>
  </div>
</footer>
</body>
</html>
```